Audio/ Video Packaging Design for a Technology company.

We need a packaging design for a bag that is 7" wide and 10" high. The design will be for a new line of audio/video products. We would like to see designs that represent a superior quality product that provides a pure connection. We want the equivalent of a nice retail bag that you would find in a store like Tallow Mart. It should be a maximum of three colors. We really want something sharp, professional and eye catching, not whimsical or cartoonish. I've included a couple of examples below. I don't really like the designs of the bags, but I want you to see examples of what I'm looking for.

The company logo, which is uploaded, should be on the design. The words "audio and video products" should be either underneath the logo or to the side. Also, somewhere on the bag, we would like the words "For a Pure Connection"

The winner of this contest will likely get the opportunity for additional work as we have more products ready to launch.

Target Market(s)

resellers, consumers - men 25-60

Industry/Entity Type

It Company

Requirements
Must have
• It should be a maximum of three colors. We really want something sharp, professional and eye catching, not whimsical or cartoonish
Nice to have
• Eye-catching design. Utilize the entire bag but don't make it too busy.
Should not have
• Whimsical, cartoonish

```html
<!DOCTYPE html>
<html lang="en">
<head>
<meta charset="utf-8">
<title>Norvane Package Design</title>
<link href="https://fonts.googleapis.com/css2?family=Montserrat:wght@400;500;600&display=swap" rel="stylesheet">
<style>
  :root {
    --stage: #8a8a8a;
    --bag: #ffffff;
    --ink: #3a3d42;
    --sky: #5bb8ee;
    --blue: #3f7fc8;
    --cable-light: #d8d8d8;
    --cable-dark: #4a4a4a;
    --trace-grey: #9a9a9a;
    --trace-blue: #a9d0f2;
    --hole: #5e5e5e;
  }
  * { box-sizing: border-box; margin: 0; padding: 0; }
  html, body { width: 1200px; height: 960px; overflow: hidden; }
  body {
    background: var(--stage);
    font-family: "Montserrat", sans-serif;
    position: relative;
  }
  .presentation-title {
    position: absolute; right: 52px; top: 52px; text-align: right;
  }
  .presentation-title .brand {
    font-size: 50px; font-weight: 500; letter-spacing: 2px; color: var(--ink);
  }
  .presentation-title .label {
    margin-top: 10px; font-size: 21px; font-weight: 500; letter-spacing: 1px; color: #eeeeee;
  }
  .bag {
    position: absolute; top: 206px; width: 483px; height: 712px;
    background: var(--bag); border-radius: 30px; overflow: hidden;
    box-shadow: 0 8px 24px rgba(0,0,0,0.25);
  }
  .bag--grey { left: 61px; }
  .bag--blue { left: 654px; }
  .hang-hole {
    position: absolute; left: 183px; top: 26px; width: 115px; height: 38px;
    background: var(--hole); border-radius: 19px;
  }
  .seal-line {
    position: absolute; left: 10px; right: 10px; top: 94px;
    border-top: 1px dashed #e2e2e2;
  }
  .wordmark {
    position: absolute; left: 75px; top: 122px; height: 210px;
    writing-mode: vertical-rl; transform: rotate(180deg);
    font-size: 50px; font-weight: 500; letter-spacing: 3px; color: var(--ink);
    line-height: 44px; text-align: left;
  }
  .brand-square {
    position: absolute; left: 80px; top: 344px; width: 38px; height: 38px;
    background: var(--blue);
  }
  .product-line {
    position: absolute; left: 124px; top: 122px; height: 290px;
    writing-mode: vertical-rl; transform: rotate(180deg);
    font-size: 16px; letter-spacing: 2px; color: var(--sky); line-height: 20px;
  }
  .origin-note {
    position: absolute; left: 14px; top: 600px; height: 90px;
    writing-mode: vertical-rl; transform: rotate(180deg);
    font-size: 6px; color: #b0b0b0;
  }
  .slogan {
    position: absolute; left: 0; right: 0; top: 646px; text-align: center;
    font-size: 21px; font-weight: 500; color: var(--blue);
  }
  .bag-art { position: absolute; inset: 0; }
</style>
</head>
<body>
  <header class="presentation-title">
    <div class="brand">NORVANE</div>
    <div class="label">PACKAGE DESIGN</div>
  </header>

  <section class="bag bag--grey">
    <svg class="bag-art" width="483" height="712" viewBox="0 0 483 712">
      <defs>
        <linearGradient id="cableGrey" x1="0" y1="0" x2="1" y2="1">
          <stop offset="0" stop-color="#e6e6e6"/>
          <stop offset="0.5" stop-color="#8c8c8c"/>
          <stop offset="1" stop-color="#4a4a4a"/>
        </linearGradient>
        <linearGradient id="circuitGrey" x1="0" y1="0" x2="0" y2="1">
          <stop offset="0" stop-color="#ffffff"/>
          <stop offset="1" stop-color="#c4c4c4"/>
        </linearGradient>
      </defs>
      <path role="img" aria-label="Window showing the coiled black audio cable" d="M231 128 H483 V419 H231 Q211 419 211 399 V148 Q211 128 231 128 Z" fill="url(#cableGrey)"/>
      <rect role="img" aria-label="Grey circuit board trace pattern" x="0" y="470" width="180" height="242" fill="url(#circuitGrey)"/>
      <rect role="img" aria-label="Grey circuit board trace pattern" x="370" y="440" width="113" height="272" fill="url(#circuitGrey)"/>
    </svg>
    <div class="hang-hole"></div>
    <div class="seal-line"></div>
    <div class="wordmark">NORVANE</div>
    <div class="brand-square"></div>
    <div class="product-line">audio and video products</div>
    <div class="origin-note">Printed in USA</div>
    <p class="slogan">“For a Pure Connection”</p>
  </section>

  <section class="bag bag--blue">
    <svg class="bag-art" width="483" height="712" viewBox="0 0 483 712">
      <defs>
        <linearGradient id="cableBlue" x1="0" y1="0" x2="1" y2="1">
          <stop offset="0" stop-color="#f0f0f0"/>
          <stop offset="0.5" stop-color="#8f8f8f"/>
          <stop offset="1" stop-color="#3e3e3e"/>
        </linearGradient>
        <linearGradient id="circuitBlue" x1="0" y1="0" x2="0" y2="1">
          <stop offset="0" stop-color="#ffffff"/>
          <stop offset="1" stop-color="#cfe4f7"/>
        </linearGradient>
      </defs>
      <rect role="img" aria-label="Light blue circuit board trace pattern" x="0" y="470" width="483" height="242" fill="url(#circuitBlue)"/>
      <path role="img" aria-label="Angled window showing the coiled black audio cable" d="M150 330 L483 110 V570 Z" fill="url(#cableBlue)"/>
    </svg>
    <div class="hang-hole"></div>
    <div class="seal-line"></div>
    <div class="wordmark">NORVANE</div>
    <div class="brand-square"></div>
    <div class="product-line">audio and video products</div>
    <div class="origin-note">Printed in USA</div>
    <p class="slogan">“For a Pure Connection”</p>
  </section>
</body>
</html>
```